Business Card Re-Design/Update

We'd like to update out business cards. I've included our current "Style guide" which has the colour scheme of the organisation in it. I've also included the branding files with logos etc in them.

I've also included a copy of one of our existing cards so that you can see how ugly/dated they look. I'd like a fresh modern corporate look.

Target Market(s)

These are for our clients, potential clients, industry contacts - like all business cards

Contact Information for Business Card

Name
Position
Company Address - Level 1, 47 Fernby Street, Carlow Qld 4072
Direct Phone
mobile
Email
Website -www.korvalit.com.au
Logo

Colors

Designer to choose colors to be used in the design.

Requirements
Must have
• Main Logo
• Cards will need to be editable to be able to personalize them for each new employee.
Nice to have
• The MapOut, ShipWell, KeepSteady would be okay to have if they can be sensibly and professionally added to the look without detracting from the main imagery.
• Maybe they could go on the back of the card? will leave this to your creative discretion as to whether/where they fit.
Should not have
• Should not have decorative or script fonts

```html
<!DOCTYPE html>
<html lang="en">
<head>
<meta charset="utf-8">
<title>korvalIT business card</title>
<link rel="stylesheet" href="https://fonts.googleapis.com/css2?family=Roboto:wght@400;500;700&family=Roboto+Condensed:wght@500&display=swap">
<style>
  :root {
    --backdrop: #9b9b9b;
    --card-red: #c0141c;
    --card-red-deep: #a70f17;
    --card-red-soft: #cf2a2e;
    --card-white: #eeeeef;
    --ink-light: #f1ecec;
    --ink-dark: #2a2a2c;
    --rule-grey: #8a8a8a;
    --tag-green: #5c9b2f;
    --tag-blue: #1f72b8;
    --tag-magenta: #a11d7e;
    --accent-red: #c4161f;
  }
  * { box-sizing: border-box; margin: 0; padding: 0; }
  html, body {
    width: 1105px;
    height: 1200px;
    overflow: hidden;
    background: var(--backdrop);
  }
  .card {
    position: absolute;
    left: 182px;
    width: 747px;
    height: 427px;
    overflow: hidden;
  }
  .card-front {
    top: 119px;
    background: linear-gradient(135deg, var(--card-red-soft) 0%, var(--card-red) 45%, var(--card-red-deep) 100%);
    color: var(--ink-light);
    font-family: "Roboto", sans-serif;
  }
  .front-decoration {
    position: absolute;
    left: 0;
    top: 0;
    width: 460px;
    height: 427px;
    background: radial-gradient(ellipse at 45% 55%, rgba(140, 8, 14, 0.35) 0%, rgba(140, 8, 14, 0.12) 50%, rgba(140, 8, 14, 0) 75%);
  }
  .front-brand {
    position: absolute;
    left: 420px;
    top: 75px;
    font-weight: 500;
    font-size: 41px;
    letter-spacing: -0.5px;
    color: var(--ink-light);
  }
  .holder {
    position: absolute;
    left: 47px;
    top: 186px;
  }
  .holder-name {
    font-family: "Roboto Condensed", sans-serif;
    font-weight: 500;
    font-size: 24px;
    letter-spacing: 0.3px;
    text-transform: uppercase;
  }
  .holder-role {
    font-size: 17px;
    margin-top: 2px;
  }
  .holder-rule {
    position: absolute;
    left: 0;
    top: 246px;
    width: 302px;
    height: 1px;
    background: rgba(255, 255, 255, 0.75);
  }
  .address {
    position: absolute;
    left: 420px;
    top: 190px;
    font-size: 17.5px;
    line-height: 22px;
  }
  .contact-list {
    position: absolute;
    left: 424px;
    top: 243px;
    list-style: none;
    font-size: 17.5px;
    line-height: 23.5px;
  }
  .contact-list li {
    display: flex;
    align-items: center;
    gap: 9px;
  }
  .contact-list svg {
    width: 16px;
    height: 16px;
    fill: var(--ink-light);
    flex: none;
  }
  .card-back {
    top: 637px;
    background: var(--card-white);
    font-family: "Roboto", sans-serif;
  }
  .back-brand {
    position: absolute;
    left: 0;
    top: 170px;
    width: 100%;
    display: flex;
    justify-content: center;
    align-items: center;
    gap: 18px;
  }
  .brand-square {
    width: 46px;
    height: 46px;
    background: var(--accent-red);
  }
  .brand-name {
    font-weight: 500;
    font-size: 64px;
    letter-spacing: -1px;
    color: var(--ink-dark);
  }
  .services {
    position: absolute;
    left: 0;
    top: 352px;
    width: 100%;
    display: flex;
    justify-content: center;
    align-items: center;
    list-style: none;
    font-weight: 500;
    font-size: 31px;
  }
  .services li + li {
    border-left: 2px solid var(--rule-grey);
    margin-left: 20px;
    padding-left: 20px;
  }
  .service-map { color: var(--tag-green); }
  .service-ship { color: var(--tag-blue); }
  .service-keep { color: var(--tag-magenta); }
</style>
</head>
<body>

<section class="card card-front">
  <div class="front-decoration" role="img" aria-label="Large faint brand symbol decoration in deeper red tones"></div>

  <div class="front-brand">korvalIT</div>

  <div class="holder">
    <div class="holder-name">Maren Tolley</div>
    <div class="holder-role">Business Development Manager</div>
  </div>
  <div class="holder-rule"></div>

  <address class="address" style="font-style: normal;">
    Level 1, 47 Fernby Street<br>
    Carlow Qld 4072
  </address>

  <ul class="contact-list" style="top: 247px;">
    <li>
      <svg viewBox="0 0 16 16" aria-hidden="true"><path d="M3.6 1.5l2.2 2.6-1.3 1.7c.9 2 2.4 3.5 4.4 4.4l1.7-1.3 2.6 2.2-1.5 2.2C6.8 14.8 1.2 9.2 1.5 3z"/></svg>
      <span>+61 (0)7 3184 5520</span>
    </li>
    <li>
      <svg viewBox="0 0 16 16" aria-hidden="true"><path d="M3.6 1.5l2.2 2.6-1.3 1.7c.9 2 2.4 3.5 4.4 4.4l1.7-1.3 2.6 2.2-1.5 2.2C6.8 14.8 1.2 9.2 1.5 3z"/></svg>
      <span>+61 (0)7 3184 5527</span>
    </li>
    <li>
      <svg viewBox="0 0 16 16" aria-hidden="true"><path d="M4.5 1h7a1 1 0 0 1 1 1v12a1 1 0 0 1-1 1h-7a1 1 0 0 1-1-1V2a1 1 0 0 1 1-1zm.8 2v9h5.4V3zM8 12.6a.8.8 0 1 0 0 1.6.8.8 0 0 0 0-1.6z"/></svg>
      <span>+61 (0)412 604 318</span>
    </li>
    <li>
      <svg viewBox="0 0 16 16" aria-hidden="true"><path d="M4 1h8v4H4zM1 6h14v6h-3v3H4v-3H1zm4 5v3h6v-3z"/></svg>
      <span>+61 (0)7 3184 5501</span>
    </li>
    <li>
      <svg viewBox="0 0 16 16" aria-hidden="true"><path d="M1 3.5h14v9H1zm1.6 1.2L8 8.7l5.4-4z"/></svg>
      <span>mtolley@korvalit.com.au</span>
    </li>
    <li>
      <svg viewBox="0 0 16 16" aria-hidden="true"><path d="M8 1a7 7 0 1 0 0 14A7 7 0 0 0 8 1zm-1 2.3v2.2L5 7l.8 2L8 9.6l.6 2.2-1 1.6a5.4 5.4 0 0 1-.6-10.1zm3 .5a5.4 5.4 0 0 1 2.6 6.7l-1.4-1.2-.6-2.3 1-1.5z"/></svg>
      <span>www.korvalit.com.au</span>
    </li>
  </ul>
</section>

<section class="card card-back">
  <div class="back-brand">
    <span class="brand-square"></span>
    <span class="brand-name">korvalIT</span>
  </div>

  <ul class="services">
    <li class="service-map">MapOut</li>
    <li class="service-ship">ShipWell</li>
    <li class="service-keep">KeepSteady</li>
  </ul>
</section>

</body>
</html>
```